Dietary supplement, Clean and simple.

Hi,
I’d like to talk about the project,

About us:
We are a dietary supplement (Vitamins, Minerals, amino acids etc.) company.
The goal is to have about 25 products at the end of this year. However, for this goal to be achieved we need a good label design to make our products represent our company values.
I’ll be here every day supporting your questions, we are fully committed to making the highest/best quality/customer experience possible.

About the design and our values:
- Professional (We are in the industry of professionalism and expertise. I would love to show we are competent at this, Id. Like to have the labels looks like we have done our research.)
- Efficient (White spacing, good use of the space available.)
- Simple (Straight forward, in 5 seconds they have to know what the product they have is/how functions. We’re trying to simplify it for the consumer.
- No distractions (the only visually “distracting” factor can be the vector art.)

The guidelines:
The goal is to have a universal design, with one element that changes (Vector art). I’ll attach a file/multiple files I think can show some visuals on what I’m looking for, and what parts of the design I think are good/bad.

Label size: 69x155mm (Front is 77.5mm)

Design whatever you think fits our image. You’re the design expert, all I care about is that it fits our company standards/image.

Use this color/font.
Font: Sans Serif
Main company color is Mind green #237D62 (Use this color for something in the design.)

What I thought would be cool/might looks ugly, who knows:
1. The front of the label: Should have 1 vector art, preferably in the top right corner. (That looks good in multiple colors. The vector can have multiple areas to color, I would prefer 2 main colors in the vector art. The interchangeable colors are used for multiple kinds of products.)
2. Text/product information on the left. The text that will have to be displayed:
- Product name for instance “Magnesium + B6”
- Description for the product for instance “Magnesium with ginger taste”
- Company name or logo. (Add ® behind it. We are soon to be trademark registered.)
3. We need to show the "daily intake" amount on the front and also the amount in the complete bottle. For instance, “Daily intake 1 capsule, 60 capsules”.
• You don’t have to design the backside of the label. After I chose a design, I’d like to chat and give specific information on what areas need to be assigned where. (Too complex because of the law.)
Updates

Hi, Please make the deadline 31 days total. I want designers to have the time to design. And not be rushed to finish it.

I want to extend the deadline because i feel like a slightly more medical look would be interesting. Hope you can come up with something!!

Target Market(s)

Dietary supplement consumers

Industry/Entity Type

Dietary supplements

Font styles to use
Sans Serif

Colors

Designer to choose colors to be used in the design.

Requirements
Must have
• Trademark icon "®" has to be at the top right after the company logo(text of logo)/name.

```html
<!DOCTYPE html>
<html lang="en">
<head>
<meta charset="UTF-8">
<title>Calm Crest – Vitamin D3 Label</title>
<link rel="stylesheet" href="https://fonts.googleapis.com/css2?family=IBM+Plex+Sans:wght@300;400;600;700&display=swap">
<style>
  :root {
    --band-grey: #bcbec0;
    --ink: #231f20;
    --mint-green: #237d62;
    --blue-light: #3b74ba;
    --blue-deep: #2a2d6f;
    --paper: #ffffff;
  }
  * { margin: 0; padding: 0; box-sizing: border-box; }
  html, body { width: 1200px; height: 1200px; overflow: hidden; background: var(--paper); }
  .label {
    position: relative;
    width: 1200px;
    height: 1200px;
    background: var(--paper);
    font-family: "IBM Plex Sans", Arial, sans-serif;
    color: var(--ink);
  }
  .band { position: absolute; left: 0; width: 1200px; height: 66px; background: var(--band-grey); }
  .band--top { top: 0; }
  .band--bottom { top: 1134px; }

  .art-panel {
    position: absolute;
    left: 232px; top: 66px;
    width: 310px; height: 387px;
    background: linear-gradient(to bottom, var(--blue-light), var(--blue-deep));
  }

  .text-line { position: absolute; line-height: 1; white-space: nowrap; }
  .brand-name {
    left: 234px; top: 493px;
    font-size: 50px; font-weight: 400; letter-spacing: 0.01em;
  }
  .brand-name sup { font-size: 24px; vertical-align: 22px; margin-left: 6px; }
  .product-name {
    left: 232px; top: 559px;
    font-size: 88px; font-weight: 600; letter-spacing: 0.01em;
  }
  .divider {
    position: absolute; left: 232px; top: 701px;
    width: 310px; height: 8px;
    background: linear-gradient(to right, var(--blue-light), var(--blue-deep));
  }
  .product-desc {
    left: 233px; top: 731px;
    font-size: 51px; font-weight: 300; letter-spacing: 0.01em;
  }

  .dotted-rule { position: absolute; left: 232px; top: 938px; }

  .capsule-icon { position: absolute; left: 231px; top: 978px; }
  .count-number {
    left: 291px; top: 986px;
    font-size: 27px; font-weight: 600; color: var(--mint-green);
  }
  .count-unit {
    left: 291px; top: 1018px;
    font-size: 27px; font-weight: 300;
  }

  .brand-mark {
    position: absolute; left: 523px; top: 1000px; width: 154px;
    display: flex; align-items: center; justify-content: center; gap: 8px;
  }
  .brand-mark__dot { width: 14px; height: 14px; border-radius: 50%; background: var(--mint-green); }
  .brand-mark__name {
    font-size: 26px; font-weight: 600; color: var(--mint-green); white-space: nowrap; line-height: 1;
  }

  .intake { position: absolute; right: 253px; text-align: right; line-height: 1; white-space: nowrap; }
  .intake-label { top: 986px; font-size: 27px; font-weight: 300; }
  .intake-amount { top: 1018px; font-size: 27px; font-weight: 600; color: var(--mint-green); }
  .intake-rule { position: absolute; left: 966px; top: 979px; width: 3px; height: 77px; background: var(--mint-green); }
</style>
</head>
<body>
  <main class="label">
    <div class="band band--top"></div>

    <div class="art-panel" role="img" aria-label="Interchangeable product vector art area in blue tones"></div>

    <p class="text-line brand-name">CALM CREST<sup>®</sup></p>
    <h1 class="text-line product-name">Vitamin D3</h1>
    <div class="divider"></div>
    <p class="text-line product-desc">Vitamin D3 2000iu</p>

    <svg class="dotted-rule" width="738" height="4" viewBox="0 0 738 4" aria-hidden="true">
      <line x1="1" y1="2" x2="737" y2="2" stroke="var(--mint-green)" stroke-width="3" stroke-dasharray="6 15.6" stroke-linecap="round"/>
    </svg>

    <svg class="capsule-icon" width="42" height="80" viewBox="0 0 42 80" aria-hidden="true">
      <rect x="1.5" y="1.5" width="39" height="77" rx="19.5" fill="none" stroke="var(--mint-green)" stroke-width="2.6"/>
    </svg>
    <p class="text-line count-number">60</p>
    <p class="text-line count-unit">SOFTGELS</p>

    <div class="brand-mark">
      <span class="brand-mark__dot"></span>
      <span class="brand-mark__name">CALM CREST</span>
    </div>

    <p class="intake intake-label">DAILY INTAKE</p>
    <p class="intake intake-amount">1 SOFTGEL</p>
    <div class="intake-rule"></div>

    <div class="band band--bottom"></div>
  </main>
</body>
</html>
```